Advertising company unique advertising platform

we need a logo design for a new company based in Australia Melbourne. We develop innovated advertising platform where consumer can use this platform to get regular discount, as business owner they can use this platform for free advertisement. Payment for this advertisement platform only payable every two weeks, when I generate revenue for their business

Industry/Entity Type

Advertising

Contact Information for Business Card

Dale Morven | Co-Founder |Managing Director
Suite 718 240 Wattlebrook Lane Melbourne Vic 3000

ABN 38 614 207 923
Tel: +61 0487 259 318 | Email: dale.morven@plivorantu.com

Font styles to use
Decorative
Script

Requirements
Must have
• Try few different design and some round corner business card
Should not have
• One round corner business card...try 4 different colour background not only black, make sure two side is designed. Be creative so imagine you are giving this to a client make sure has wow factor, if you can also try one design with engrave like all the logo, words look 3d feel
• The word Advertising Platform use attached file font

```html
<!DOCTYPE html>
<html lang="en">
<head>
<meta charset="utf-8">
<title>Kestrelo Hub – Business Card</title>
<link href="https://fonts.googleapis.com/css2?family=Source+Sans+3:wght@400;600;700&display=swap" rel="stylesheet">
<style>
  :root {
    --backdrop: #e9e6e1;
    --card-dark: #2a2a2a;
    --ink: #1c1410;
    --orange-hot: #e4472d;
    --orange-warm: #f0883a;
    --orange-glow: #f4c24a;
    --teal: #22e0b0;
    --sky: #3ab6ec;
    --brand-teal: #2fd8b4;
    --brand-orange: #ef5a2e;
    --web-text: #e8e8e8;
  }
  * { box-sizing: border-box; margin: 0; padding: 0; }
  html, body { width: 1200px; height: 960px; overflow: hidden; }
  body {
    background: var(--backdrop);
    font-family: "Source Sans 3", "Segoe UI", sans-serif;
    position: relative;
  }
  .card {
    position: absolute;
    width: 600px;
    height: 342px;
    border-radius: 22px;
    background: var(--card-dark);
    overflow: hidden;
  }
  .card--front { left: 315px; top: 113px; }
  .card--back  { left: 312px; top: 473px; }
  .card__art { position: absolute; inset: 0; }

  .brand {
    position: absolute;
    display: flex;
    align-items: center;
    gap: 12px;
  }
  .brand__dot {
    width: 34px; height: 34px;
    border-radius: 50%;
    background: var(--brand-orange);
    flex: none;
  }
  .brand__name {
    font-weight: 700;
    color: var(--brand-teal);
    white-space: nowrap;
    line-height: 1;
  }
  .card--front .brand { left: 40px; top: 150px; }
  .card--front .brand__name { font-size: 36px; }
  .card--back .brand { left: 0; right: 0; top: 140px; justify-content: center; }
  .card--back .brand__dot { width: 44px; height: 44px; }
  .card--back .brand__name { font-size: 48px; }

  .contact {
    position: absolute;
    right: 28px;
    top: 126px;
    text-align: right;
    color: var(--ink);
    font-size: 15px;
    line-height: 20px;
  }
  .contact__name { font-weight: 700; font-size: 17px; line-height: 22px; }
  .contact__role { font-size: 17px; line-height: 22px; }
  .contact__company { margin-top: 5px; }
  .contact__address { margin-top: 4px; }
  .contact__line { display: flex; justify-content: flex-end; align-items: center; gap: 6px; }
  .contact__line svg { width: 13px; height: 13px; flex: none; }

  .website {
    position: absolute;
    left: 0; right: 0;
    top: 294px;
    text-align: center;
    color: var(--web-text);
    font-size: 14px;
    letter-spacing: 5px;
  }
</style>
</head>
<body>

<section class="card card--front" aria-label="Business card front">
  <svg class="card__art" viewBox="0 0 600 342" aria-hidden="true">
    <defs>
      <radialGradient id="warm-field" cx="0.62" cy="0.35" r="0.7">
        <stop offset="0" stop-color="var(--orange-glow)"/>
        <stop offset="0.45" stop-color="var(--orange-warm)"/>
        <stop offset="1" stop-color="var(--orange-hot)"/>
      </radialGradient>
      <linearGradient id="swoosh" x1="0" y1="1" x2="1" y2="0">
        <stop offset="0" stop-color="var(--teal)"/>
        <stop offset="0.55" stop-color="#6c8fd8"/>
        <stop offset="1" stop-color="var(--sky)"/>
      </linearGradient>
    </defs>
    <path d="M445 0 C470 70 425 150 335 215 C270 262 240 305 248 342 L600 342 L600 0 Z" fill="url(#warm-field)"/>
    <path d="M426 5 C452 92 402 162 318 222 C262 262 238 288 240 300 C252 274 282 250 332 214 C414 158 446 92 426 5 Z" fill="url(#swoosh)"/>
  </svg>

  <div class="brand">
    <span class="brand__dot"></span>
    <span class="brand__name">Kestrelo Hub</span>
  </div>

  <div class="contact">
    <div class="contact__name">DALE MORVEN</div>
    <div class="contact__role">CO-FOUNDER</div>
    <div class="contact__role">MANAGING DIRECTOR</div>
    <div class="contact__company">Plivorantu</div>
    <div>ABN 38 614 207 923</div>
    <div class="contact__address">Suite 718 240</div>
    <div>Wattlebrook Lane, Melbourne Vic 3000</div>
    <div class="contact__line">
      <span>+61 0487 259 318</span>
      <svg viewBox="0 0 16 16" aria-hidden="true"><path d="M2 6 C2 3 14 3 14 6 L11 7 L10 5.5 L6 5.5 L5 7 Z M4 8 L12 8 L13.5 13 L2.5 13 Z" fill="var(--ink)"/></svg>
    </div>
    <div class="contact__line">
      <span>dale.morven@plivorantu.com</span>
      <svg viewBox="0 0 16 16" aria-hidden="true"><rect x="2" y="4" width="12" height="9" fill="var(--ink)"/><path d="M2 4 L8 9 L14 4" stroke="var(--orange-warm)" stroke-width="1.2" fill="none"/></svg>
    </div>
  </div>
</section>

<section class="card card--back" aria-label="Business card back">
  <div class="brand">
    <span class="brand__dot"></span>
    <span class="brand__name">Kestrelo Hub</span>
  </div>
  <div class="website">www.plivorantu.com</div>
</section>

</body>
</html>
```